Smart, Classy, Conservative looking Legal Letterhead

I need a letterhead that when you look at it it "says to you " this is a well established law firm with very smart lawyers, which will one day be appearing before the Supreme Court of the USA. All information about the Law firm should appear at the top of the page. please no information in the footer.

Industry/Entity Type

Legal

Requirements
Must have
• The name of the law firm, both addresses, phone number and fax,, The names of the attorneys, the website.
• Fields that get changed such as the date, VIA, Address of who the letter is going to,
• Re, Index,
• should have a clean neat look, sleek
Nice to have
• some color would be nice. A logo of some sort could be nice as well. Maybe a single S or interlocking M's For Merriton and Merriton.
Should not have
• not too modern looking.

```html
<!DOCTYPE html>
<html lang="en">
<head>
<meta charset="utf-8">
<title>Merriton &amp; Merriton Letterhead</title>
<link rel="stylesheet" href="https://fonts.googleapis.com/css2?family=Tinos:ital,wght@0,400;0,700;1,400&display=swap">
<style>
  :root {
    --backdrop: #e9e6e1;
    --paper: #ffffff;
    --ink: #111111;
    --gold: #b8961e;
    --band-brown: #9a6a1c;
    --band-mid: #c09527;
    --band-gold: #dcbc2a;
    --band-olive: #8e8a3a;
    --cc-text: #fbf5dc;
  }
  * { margin: 0; padding: 0; box-sizing: border-box; }
  html, body {
    width: 1200px; height: 700px; overflow: hidden;
    background: var(--backdrop);
    font-family: "Tinos", "Times New Roman", serif;
    color: var(--ink);
  }
  .letterhead {
    position: absolute; left: 362px; top: 19px;
    width: 476px; height: 662px;
    background: var(--paper);
    box-shadow: 0 2px 10px rgba(0,0,0,0.15);
    color: var(--ink);
  }
  .firm-mark {
    position: absolute; left: 14px; top: 60px;
    display: flex; align-items: center; gap: 5px;
    color: var(--gold); font-weight: 700; font-size: 11px;
  }
  .mark-dot { width: 10px; height: 10px; border-radius: 50%; background: var(--gold); }
  .firm-header {
    position: absolute; left: 118px; top: 18px; width: 240px;
    text-align: center; line-height: 1.1;
  }
  .firm-name { font-size: 16px; font-weight: 700; }
  .firm-title { font-size: 14px; font-weight: 700; }
  .firm-address, .firm-web { font-size: 8.5px; line-height: 1.3; }
  .firm-web { margin-top: 4px; }
  .letter-date { font-style: italic; font-size: 12px; margin-top: 6px; }
  .recipient {
    position: absolute; left: 12px; top: 130px;
    font-size: 7.5px; line-height: 1.45; font-style: normal;
  }
  .delivery { font-weight: 700; }
  .attorney-list {
    position: absolute; right: 10px; top: 130px;
    text-align: right; font-size: 7.5px; font-weight: 700; line-height: 1.45;
    list-style: none;
  }
  .reference {
    position: absolute; left: 138px; top: 204px;
    font-size: 7.5px; line-height: 1.4;
  }
  .reference b { font-weight: 700; }
  .letter-body {
    position: absolute; left: 12px; top: 236px; width: 452px;
    font-size: 7.5px; line-height: 1.45;
  }
  .letter-body p { margin-bottom: 9px; }
  .letter-body .indent { text-indent: 80px; }
  .signoff { line-height: 1.45; }
  .footer-band {
    position: absolute; left: 0; bottom: 0; width: 100%; height: 64px;
    background: linear-gradient(90deg, var(--band-brown) 0%, var(--band-mid) 40%, var(--band-gold) 70%, var(--band-olive) 100%);
  }
  .cc {
    position: absolute; left: 12px; bottom: 12px;
    font-size: 7px; color: var(--cc-text);
  }
  .cc b { font-weight: 700; }
  .band-mark {
    position: absolute; right: 14px; top: 22px;
    font-size: 10px; font-weight: 700; color: var(--paper);
  }
</style>
</head>
<body>
  <article class="letterhead">
    <div class="firm-mark"><span class="mark-dot"></span><span>Merriton</span></div>

    <header class="firm-header">
      <div class="firm-name">MERRITON &amp; MERRITON</div>
      <div class="firm-title">ATTORNEYS AT LAW</div>
      <div class="firm-address">414 MADE UP STREET<br>TOWN, STATE 39440</div>
      <div class="firm-web">WWW.WEBSITE.COM</div>
      <div class="letter-date">July 1st 2015</div>
    </header>

    <address class="recipient">
      <div class="delivery">VIA SWIFTPOST</div>
      Hon. Fake Judge Name Here<br>
      Harbor State District Court, H.D.S<br>
      200 Justice Square<br>
      Courtroom 99999<br>
      Harbor Vale, HS 11900-0000
    </address>

    <ul class="attorney-list">
      <li>Daniel A. Merriton</li>
      <li>Walter J. Penhale</li>
      <li>Gregory T. Ashworth</li>
      <li>Helen M. Crandall</li>
      <li>Oliver K. Dunmore</li>
      <li>Ruth E. Halloway</li>
    </ul>

    <div class="reference">
      <div><b>Re:</b> XXXXXXXXXXXXXXXXXXXXXXXXXXXXXXXXX</div>
      <div><b>Index:</b> XXXXXXXXXXXXXXXXXXXXXXXXXXXXXXXXX</div>
    </div>

    <section class="letter-body">
      <p>Your Honour,</p>
      <p class="indent">Pursuant to Your Honor's Individual Practises Rule III(C)(3), enclosed please find a courtesy copy of Plaintiffs Revised. Lorem ipsum dolor sit amet, consectetur adipiscing elit, sed do eiusmod tempor incididunt ut labore et dolore magna aliqua. Ut enim ad minim veniam, quis nostrud exercitation ullamco laboris nisi ut aliquip ex ea commodo consequat.</p>
      <p>Duis aute irure dolo in reprehenderit in voluptate velit esse cillum dolore eu fugiat nulla pariatur. Excepteur sint occaecat cupidatat non proident, sunt in culpa qui officia deserunt mollit anim id est laborum.</p>
      <div class="signoff">Respectfully,<br>Daniel A. Merriton</div>
    </section>

    <footer class="footer-band">
      <span class="band-mark">Merriton</span>
      <span class="cc"><b>CC:</b> Fake opposing counsel name here</span>
    </footer>
  </article>
</body>
</html>
```